Quorva - corporate Business Card

We need a good look and innovative business card for a new start up company based in Los Angeles called "Quorva". We are in a payment business, including payment card, app, and ewallet. We are expert in online payment and Card not present (CNP) transaction.
We need an innovative, modern business card.

Our logo font is Aero Matics

Target Market(s)

Startup - Bank - Online Payment - Card Manufacturing

Industry/Entity Type

Startup

Contact Information for Business Card

phone: 555 014 7396 - Address: 4172 Marlowe blvd, Brennan Falls, OR 97299

Requirements
Must have
• Message: innovative, professional, expert, high tech, trust, online payment expert, security
Nice to have
• no comment
Should not have
• no Comment

```html
<!DOCTYPE html>
<html lang="en">
<head>
<meta charset="utf-8">
<title>Quorva – Business Card</title>
<link rel="stylesheet" href="https://fonts.googleapis.com/css2?family=Montserrat:wght@600;700&family=Open+Sans:wght@300;400&display=swap">
<style>
  :root {
    --page: #e4e4e4;
    --card: #2f2f31;
    --card-back: #262628;
    --band: #1b1b1d;
    --red: #c8252d;
    --red-edge: #d8222b;
    --white: #f4f4f4;
    --muted: #cfcfcf;
  }
  * { box-sizing: border-box; margin: 0; padding: 0; }
  html, body { width: 1200px; height: 1000px; overflow: hidden; }
  body {
    background: var(--page);
    font-family: "Open Sans", sans-serif;
    position: relative;
  }
  .card {
    position: absolute;
    left: 200px;
    width: 800px;
    height: 457px;
    overflow: hidden;
    border-bottom: 4px solid var(--red-edge);
    box-shadow: 0 6px 18px rgba(0,0,0,.25);
  }
  /* back side */
  .card--back { top: 30px; background: var(--card-back); }
  .pattern { position: absolute; left: 0; width: 100%; }
  .pattern--upper {
    top: 0; height: 170px;
    background: linear-gradient(90deg, #d6d6d6 0%, #8d8d8f 18%, #4a4a4c 40%, #333335 70%, #2b2b2d 100%);
    opacity: .55;
  }
  .pattern--lower {
    top: 290px; height: 167px;
    background: linear-gradient(90deg, #3a3a3c 0%, #2e2e30 50%, #2a2a2c 100%);
  }
  .band {
    position: absolute; left: 0; top: 170px; width: 100%; height: 120px;
    background: var(--band);
    display: flex; align-items: center; justify-content: center; gap: 22px;
  }
  .band .brand-dot { width: 92px; height: 92px; border-radius: 50%; background: var(--red); }
  .brand-name {
    font-family: "Montserrat", sans-serif;
    font-weight: 600;
    color: var(--red);
    letter-spacing: 3px;
    line-height: 1;
  }
  .band .brand-name { font-size: 64px; }

  /* front side */
  .card--front { top: 513px; background: var(--card); }
  .card--front .brand-name {
    position: absolute; right: 22px; top: 36px; font-size: 62px;
  }
  .card--front .brand-dot {
    position: absolute; left: 468px; top: 150px;
    width: 320px; height: 320px; border-radius: 50%; background: var(--red);
  }
  .side-bars { position: absolute; left: 0; top: 128px; width: 18px; }
  .side-bars span { display: block; width: 18px; background: var(--red); margin-bottom: 6px; }
  .side-bars .bar-name { height: 62px; }
  .side-bars .bar-address { height: 62px; }
  .side-bars .bar-phone { height: 30px; }
  .side-bars .bar-online { height: 56px; }

  .contact { position: absolute; left: 100px; top: 140px; color: var(--muted); }
  .person-name {
    font-family: "Montserrat", sans-serif; font-weight: 700;
    color: var(--white); font-size: 25px; letter-spacing: 1px;
  }
  .person-role { color: var(--red); font-size: 17px; letter-spacing: 1px; margin-top: 2px; }
  .address { margin-top: 18px; font-size: 16px; font-weight: 300; line-height: 1.4; }
  .lines { list-style: none; margin-top: 20px; margin-left: -30px; font-size: 16px; font-weight: 300; }
  .lines li { display: flex; align-items: center; gap: 14px; height: 27px; }
  .lines svg { width: 13px; height: 13px; fill: var(--red); flex: none; }
  .lines .accent { color: var(--red); }
</style>
</head>
<body>

<section class="card card--back" aria-label="Business card, back">
  <div class="pattern pattern--upper" role="img" aria-label="Repeating pattern of small brand circles fading from silver to dark"></div>
  <div class="band">
    <div class="brand-dot"></div>
    <div class="brand-name">quorva</div>
  </div>
  <div class="pattern pattern--lower" role="img" aria-label="Repeating pattern of small embossed dark brand circles"></div>
</section>

<section class="card card--front" aria-label="Business card, front">
  <div class="brand-name">quorva</div>
  <div class="brand-dot"></div>

  <div class="side-bars">
    <span class="bar-name"></span>
    <span class="bar-address"></span>
    <span class="bar-phone"></span>
    <span class="bar-online"></span>
  </div>

  <div class="contact">
    <h1 class="person-name">DANA CORVELL</h1>
    <p class="person-role">CEO &amp; FOUNDER</p>
    <p class="address">4172 Marlowe blvd,<br>Brennan Falls, OR 97299</p>
    <ul class="lines">
      <li>
        <svg viewBox="0 0 24 24"><path d="M6.6 10.8a15.1 15.1 0 0 0 6.6 6.6l2.2-2.2c.3-.3.7-.4 1-.2 1.1.4 2.3.6 3.6.6.6 0 1 .4 1 1V20c0 .6-.4 1-1 1A17 17 0 0 1 3 4c0-.6.4-1 1-1h3.5c.6 0 1 .4 1 1 0 1.3.2 2.5.6 3.6.1.3 0 .7-.2 1z"/></svg>
        <span>555 014 7396</span>
      </li>
      <li>
        <svg viewBox="0 0 24 24"><path d="M2 5h20v14H2z"/><path d="M2 6l10 7.5L22 6V5H2z" fill="#2f2f31"/></svg>
        <span>yourname@email.com</span>
      </li>
      <li>
        <svg viewBox="0 0 24 24"><circle cx="12" cy="12" r="10"/><path d="M2 12h20M12 2c3 3 3 17 0 20M12 2c-3 3-3 17 0 20" stroke="#2f2f31" stroke-width="1.6" fill="none"/></svg>
        <span>www.<span class="accent">websitename</span>.com</span>
      </li>
    </ul>
  </div>
</section>

</body>
</html>
```